Business Card Design for Training Business

Clear Path Coaching is a new business that delivers training and other services with a focus on topics related to mental health and wellbeing, for example, Wellmind Response Course, Resilience etc. We have a strong focus on evidence-based psychology and neuroscience. I have a logo which I will upload with the brief, so please consider colours that work well with the logo.
Target Market(s)
Adults, workplaces (particularly government and not-for-profits)
Industry/Entity Type
Business
Contact Information for Business Card
Head Strong TrainingSamantha SellwoodDirector0438 770 850sam@headstrongtraining.com.auwww.headstrongtraining.com.au

```html
<!DOCTYPE html>
<html lang="en">
<head>
<meta charset="utf-8">
<title>Clear Path Coaching – Business Card</title>
<link href="https://fonts.googleapis.com/css2?family=Lato:wght@300;400&display=swap" rel="stylesheet">
<style>
  :root {
    --backdrop: #e9e6e1;
    --card-black: #0c0c0d;
    --mint: #a9dccf;
    --mint-soft: #bfe6dc;
    --ink: #2a2d2c;
    --rule: #6f8a83;
  }
  * { margin: 0; padding: 0; box-sizing: border-box; }
  html, body {
    width: 1200px;
    height: 1023px;
    overflow: hidden;
    background: var(--backdrop);
    font-family: "Lato", sans-serif;
  }
  .card {
    position: absolute;
    left: 150px;
    top: 255px;
    width: 900px;
    height: 514px;
    background: var(--card-black);
    box-shadow: 0 14px 40px rgba(0, 0, 0, 0.25);
    overflow: hidden;
  }
  .brand-band {
    position: absolute;
    left: 0; top: 0;
    width: 100%;
    height: 230px;
    display: flex;
    align-items: center;
    padding-left: 150px;
    gap: 26px;
  }
  .brand-mark {
    width: 78px;
    height: 78px;
    flex: none;
  }
  .brand-name {
    color: var(--mint);
    font-weight: 300;
    font-size: 34px;
    letter-spacing: 0.14em;
    text-transform: uppercase;
  }
  .info-panel {
    position: absolute;
    left: 0; top: 230px;
    width: 100%;
    height: 284px;
    background: linear-gradient(180deg, var(--mint-soft), var(--mint));
    color: var(--ink);
  }
  .contact-list {
    position: absolute;
    left: 430px;
    top: 34px;
    list-style: none;
  }
  .contact-list li {
    display: flex;
    align-items: center;
    gap: 14px;
    font-size: 21px;
    font-weight: 300;
    line-height: 36px;
  }
  .contact-icon {
    width: 18px;
    height: 18px;
    flex: none;
  }
  .divider {
    position: absolute;
    left: 150px;
    top: 154px;
    width: 620px;
    height: 1px;
    background: var(--rule);
  }
  .person {
    position: absolute;
    right: 490px;
    top: 172px;
    text-align: right;
    font-weight: 300;
  }
  .person-name {
    font-size: 30px;
    line-height: 38px;
  }
  .person-role {
    font-size: 22px;
    line-height: 30px;
    font-weight: 400;
  }
  .person-company {
    font-size: 20px;
    line-height: 28px;
  }
</style>
</head>
<body>
  <section class="card">
    <header class="brand-band">
      <svg class="brand-mark" viewBox="0 0 78 78" aria-hidden="true">
        <circle cx="39" cy="39" r="36" fill="none" stroke="var(--mint)" stroke-width="2"/>
      </svg>
      <span class="brand-name">Clear Path Coaching</span>
    </header>

    <div class="info-panel">
      <ul class="contact-list">
        <li>
          <svg class="contact-icon" viewBox="0 0 24 24" aria-hidden="true">
            <path d="M6.6 10.8a15 15 0 0 0 6.6 6.6l2.2-2.2a1 1 0 0 1 1-.25 11.4 11.4 0 0 0 3.6.6 1 1 0 0 1 1 1V20a1 1 0 0 1-1 1A17 17 0 0 1 3 4a1 1 0 0 1 1-1h3.5a1 1 0 0 1 1 1c0 1.25.2 2.45.6 3.6a1 1 0 0 1-.25 1z" fill="var(--ink)"/>
          </svg>
          0491 362 517
        </li>
        <li>
          <svg class="contact-icon" viewBox="0 0 24 24" aria-hidden="true">
            <rect x="2" y="5" width="20" height="14" rx="1.5" fill="var(--ink)"/>
            <path d="M3 6.5l9 6.5 9-6.5" fill="none" stroke="var(--mint-soft)" stroke-width="1.6"/>
          </svg>
          bec@clearpathcoaching.example.au
        </li>
        <li>
          <svg class="contact-icon" viewBox="0 0 24 24" aria-hidden="true">
            <circle cx="12" cy="12" r="10" fill="var(--ink)"/>
            <path d="M2 12h20M12 2c3 3 3 17 0 20M12 2c-3 3-3 17 0 20M4 7h16M4 17h16" fill="none" stroke="var(--mint-soft)" stroke-width="1.2"/>
          </svg>
          www.clearpathcoaching.example.au
        </li>
      </ul>

      <div class="divider"></div>

      <div class="person">
        <p class="person-name">Rebecca Tanfield</p>
        <p class="person-role">Director</p>
        <p class="person-company">Clear Path Coaching</p>
      </div>
    </div>
  </section>
</body>
</html>
```